Distribution/Printing company needs a web site to inform prospective customers on what we do.

Distribution/Printing/Packaging company needs a web site to inform prospective customers on what we do. Please look at our direct to consumer web site (under development) for an idea of the product lines we sell: storedev.maplewickhaven.com
Logo files are attached as is a flyer that is under development which contains other information about the company (this is to be used for content- not to be posted as is). The web site should be focused on our business customer base and is not intended to be direct to consumer. Site should have a link to our consumer web site.
Site design should be mobile friendly, or mobile could be redirected to a mobile version. This web site will be strictly informational and will not be designed for any sales transactions.

Target Market(s)

Manufacturing and retail businesses, any other multi-site business that would benefit from centralized pricing and budget controls we can provide (banks, medical/dental offices, educational facilities, etc).

Industry/Entity Type

It Company

Coding

Coded - Design and coding required

Number of Pages Required

5+ page

Requirements
Must have
• 1) Top level menu: Products, about us, locations, contact us, news
• 2) page with news/promotions that is easily updated
• 3) "contact us" form (name, company, phone, email address) email link
• 4) link to www.store.maplewickhaven.com with information that lower pricing is available for businesses
• 5) SEO keywords
• 6) Link to powerpoint presentation file
Nice to have
• 1) our phone number should appear on every page near the top

```html
<!DOCTYPE html>
<html lang="en">
<head>
<meta charset="utf-8">
<title>Maplewick Haven Supply – Packaging, Printing, Distribution</title>
<link rel="stylesheet" href="https://fonts.googleapis.com/css2?family=Arimo:wght@400;700&family=Open+Sans:wght@400;600&display=swap">
<style>
:root{
  --header-bg:#2b2a2b;
  --footer-bg:#262626;
  --bottom-bg:#0d0d0d;
  --accent:#ef5535;
  --menu-orange:#d95a0a;
  --submit:#f6a623;
  --text-dark:#2a2a2a;
  --text-grey:#8a8a8a;
  --footer-text:#b5b5b5;
  --field-bg:#f6f6f6;
  --field-line:#dcdcdc;
  --white:#ffffff;
}
*{box-sizing:border-box;margin:0;padding:0}
html,body{width:1033px;height:1200px;overflow:hidden;background:var(--white);font-family:"Arimo",Arial,sans-serif}
.page{position:relative;width:1033px;height:1200px;overflow:hidden}
.abs{position:absolute}

/* header */
.site-header{left:0;top:0;width:1033px;height:95px;background:var(--header-bg)}
.brand{left:120px;top:44px;width:160px;text-align:center;color:var(--white)}
.brand-name{font-weight:700;font-size:12.5px;letter-spacing:.3px;white-space:nowrap}
.brand-tag{font-size:8.5px;margin-top:3px;white-space:nowrap}
.header-phone{left:801px;top:13px;display:flex;align-items:center;gap:9px;color:var(--white);font-size:17px}
.phone-badge{width:20px;height:20px;background:var(--accent);border-radius:3px;display:flex;align-items:center;justify-content:center}
.main-nav{left:0;top:62px;width:1033px;height:32px}
.main-nav a{position:absolute;top:0;height:32px;line-height:15px;color:var(--white);font-size:12.5px;text-decoration:none;padding:0 3px}
.main-nav a.active{background:var(--menu-orange);height:32px}

.dropdown{left:395px;top:94px;width:160px;background:var(--menu-orange);padding:0 3px;font-family:"Open Sans",sans-serif}
.dropdown li{list-style:none;height:29.8px;line-height:29px;color:var(--white);font-size:12px;padding-left:6px;border-bottom:1px solid rgba(255,255,255,.75)}
.dropdown li:last-child{border-bottom:none}

/* slider */
.hero-photo{left:104px;top:138px;width:826px;height:337px;background:linear-gradient(120deg,#c9c2bb 0%,#d83a3c 25%,#c8a57a 50%,#d3363a 75%,#e4e0dc 100%)}
.hero-caption{left:704px;top:326px;color:var(--white);text-align:left}
.hero-caption strong{display:block;font-size:15px;font-weight:700}
.hero-caption span{font-size:10.5px;font-weight:700}
.slide-arrow{top:299px;width:26px;height:26px;border-radius:50%;background:#7b7b7b}
.slide-arrow.prev{left:27px}
.slide-arrow.next{left:978px}

/* services */
.services{left:0;top:475px;width:1033px;height:178px;background:var(--accent)}
.service{top:18px;width:190px;text-align:center;color:var(--white)}
.service svg{display:block;margin:0 auto;height:54px}
.service h3{font-weight:400;font-size:17px;margin-top:14px}
.service p{font-size:11px;line-height:14px;margin-top:6px}

/* content */
.section-title{font-size:15.5px;font-weight:700;color:var(--text-dark)}
.who-photo{left:104px;top:718px;width:176px;height:91px;border:1px solid #e5e5e5;background:linear-gradient(90deg,#eeeeee,#d8bb98 40%,#caa479 60%,#efefef)}
.body-copy{color:var(--text-grey);font-size:10.4px;line-height:13.7px;text-align:justify}
.quote-field{left:697px;width:233px;background:var(--field-bg);border:1px solid var(--field-line);color:#555;font-size:12px;padding:9px 8px}
.send-btn{left:829px;top:895px;width:101px;height:27px;background:var(--accent);color:var(--white);font-size:12.5px;text-align:center;line-height:27px;border-radius:2px}

/* footer */
.site-footer{left:4px;top:978px;width:1029px;height:184px;background:var(--footer-bg)}
.footer-col h4{font-weight:400;font-size:12.5px;color:var(--white)}
.footer-col ul{list-style:none;margin-top:15px}
.footer-col li{font-size:10.5px;color:var(--footer-text);height:20.7px;padding-left:2px}
.contact-line{display:flex;gap:9px;font-size:10.5px;color:var(--footer-text);line-height:12px}
.newsletter-text{font-size:10.5px;line-height:12.5px;color:var(--footer-text);text-align:justify}
.news-input{left:742px;top:1073px;width:138px;height:27px;background:var(--white);font-size:11.5px;color:#555;padding:7px 6px}
.news-submit{left:880px;top:1073px;width:50px;height:27px;background:var(--submit);color:var(--white);font-size:11.5px;text-align:center;line-height:27px}
.bottom-bar{left:0;top:1162px;width:1033px;height:38px;background:var(--bottom-bg)}
.copyright{left:103px;top:13px;color:var(--white);font-size:10.5px}
.social{top:9px;width:20px;height:20px;background:#8c8c8c;border-radius:2px}
</style>
</head>
<body>
<div class="page">

  <header class="site-header abs">
    <div class="brand abs">
      <div class="brand-name">MAPLEWICK HAVEN SUPPLY</div>
      <div class="brand-tag">Packaging • Printing • Distribution</div>
    </div>
    <div class="header-phone abs">
      <span class="phone-badge"><svg width="12" height="12" viewBox="0 0 24 24"><path fill="#2b2a2b" d="M6.6 10.8a15 15 0 0 0 6.6 6.6l2.2-2.2a1 1 0 0 1 1-.25 11 11 0 0 0 3.6.6 1 1 0 0 1 1 1V20a1 1 0 0 1-1 1A17 17 0 0 1 3 4a1 1 0 0 1 1-1h3.5a1 1 0 0 1 1 1 11 11 0 0 0 .6 3.6 1 1 0 0 1-.25 1z"/></svg></span>
      <span>555-014-2290</span>
    </div>
  </header>

  <nav class="main-nav abs">
    <a style="left:334px">Home</a>
    <a class="active" style="left:395px;width:66px">Packaging</a>
    <a style="left:486px">Office Supplies</a>
    <a style="left:597px">Janitorial</a>
    <a style="left:675px">Retail Supplies</a>
    <a style="left:789px">About Us</a>
    <a style="left:869px">Contact US</a>
  </nav>

  <div class="hero-photo abs" role="img" aria-label="Photo of opened red and kraft shipping boxes with a welcome booklet"></div>
  <div class="hero-caption abs"><strong>MAPLEWICK HAVEN SUPPLY</strong><span>Packaging • Printing • Distribution</span></div>
  <div class="slide-arrow prev abs"><svg width="26" height="26" viewBox="0 0 26 26"><path d="M18 13H8m4-4-4 4 4 4" stroke="#fff" stroke-width="1.5" fill="none"/></svg></div>
  <div class="slide-arrow next abs"><svg width="26" height="26" viewBox="0 0 26 26"><path d="M8 13h10m-4-4 4 4-4 4" stroke="#fff" stroke-width="1.5" fill="none"/></svg></div>

  <ul class="dropdown abs">
    <li>Bags - Poly</li>
    <li>Kraft Paper</li>
    <li>Bubble Wrap</li>
    <li>Tape and Tape Dispensers</li>
    <li>Packing List Envelopes</li>
    <li>Staples</li>
    <li>Corrugated Boxes</li>
    <li>Closures</li>
    <li>Tissue</li>
  </ul>

  <section class="services abs">
    <div class="service abs" style="left:102px">
      <svg viewBox="0 0 84 44" width="84"><g fill="none" stroke="#fff" stroke-width="3"><rect x="2" y="4" width="30" height="36" rx="3"/><rect x="52" y="4" width="30" height="36" rx="3"/></g><g stroke="#fff" stroke-width="3"><path d="M8 13h18M8 20h18M8 27h18M8 34h18M58 13h18M58 20h18M58 27h18M58 34h18"/></g><path d="M34 16h6v-6l10 12-10 12v-6h-6z" fill="#fff"/></svg>
      <h3>Legal Copy</h3>
      <p>Lorem ipsum dolor sit amet, con-<br>sectetur adipiscing elit. Nunc eget<br>magna enim.</p>
    </div>
    <div class="service abs" style="left:316px">
      <svg viewBox="0 0 64 56" width="64"><rect x="16" y="2" width="32" height="16" fill="#fff"/><rect x="2" y="20" width="60" height="26" rx="4" fill="#fff"/><rect x="14" y="38" width="36" height="16" fill="#fff" stroke="#ef5535" stroke-width="3"/><circle cx="52" cy="28" r="2.5" fill="#ef5535"/></svg>
      <h3>Digital Printing</h3>
      <p>Lorem ipsum dolor sit amet, con-<br>sectetur adipiscing elit. Nunc eget<br>magna enim.</p>
    </div>
    <div class="service abs" style="left:528px">
      <svg viewBox="0 0 56 60" width="52"><g fill="#fff"><rect x="14" y="2" width="40" height="18" rx="9"/><rect x="2" y="38" width="40" height="18" rx="9"/><path d="M14 11h16L30 47H14z"/></g><circle cx="45" cy="11" r="4" fill="#ef5535"/><circle cx="33" cy="47" r="4" fill="#ef5535"/></svg>
      <h3>Offset Printing</h3>
      <p>Lorem ipsum dolor sit amet, con-<br>sectetur adipiscing elit. Nunc eget<br>magna enim.</p>
    </div>
    <div class="service abs" style="left:740px">
      <svg viewBox="0 0 70 56" width="70"><path d="M2 22 35 2l33 20v32H2z" fill="#fff"/><rect x="16" y="10" width="38" height="28" fill="#fff" stroke="#ef5535" stroke-width="2"/><path d="M22 18h26M22 24h26M22 30h18" stroke="#ef5535" stroke-width="3"/><path d="M2 22l33 22 33-22M2 54l24-18M68 54 44 36" stroke="#ef5535" stroke-width="2" fill="none"/></svg>
      <h3>Mailing</h3>
      <p>Lorem ipsum dolor sit amet, con-<br>sectetur adipiscing elit. Nunc eget<br>magna enim.</p>
    </div>
  </section>

  <h2 class="section-title abs" style="left:104px;top:688px">Who We Are</h2>
  <div class="who-photo abs" role="img" aria-label="Photo of wooden triangular packaging pieces"></div>
  <p class="body-copy abs" style="left:293px;top:716px;width:332px">Lorem ipsum dolor sit amet, consectetur adipiscing elit. Nunc eget magna enim. Morbi at tortor enim, quis gravida lacus. Phasellus tempor lorem nec ipsum adipiscing mattis. Integer placerat dictum eros, vitae pulvinar neque vestibulum et. Proin imperdiet, felis vel consectetur ornare, dui leo pulvinar erat, eu dictum justo nibh vel quam. Mauris interdum vehicula enim, eu aliquet tortor volutpat sit amet. Fusce nec augue metus.</p>
  <p class="body-copy abs" style="left:104px;top:822px;width:521px">Morbi dui nisi, luctus ut faucibus ut, pellentesque nec metus. Curabitur consectetur, eros ac convallis elementum, neque nunc molestie leo, eu accumsan erat nisi sit amet quam. Quisque ac eros odio. Aliquam hendrerit pulvinar elit, at blandit tortor tincidunt non. Praesent ultricies enim est, in blandit sem. Nam tincidunt ipsum et eros tempus a sodales tortor sagittis. Ut ut dolor mauris. Quisque sed magna neque. Maecenas vel condimentum dolor.</p>

  <h2 class="section-title abs" style="left:697px;top:688px">Get a Free Quote</h2>
  <div class="quote-field abs" style="top:720px;height:31px">Name</div>
  <div class="quote-field abs" style="top:765px;height:31px">Email</div>
  <div class="quote-field abs" style="top:808px;height:76px">Write a message</div>
  <div class="send-btn abs">Send Message</div>

  <footer class="site-footer abs"></footer>
  <div class="footer-col abs" style="left:104px;top:995px">
    <h4>Navigation</h4>
    <ul><li>Home</li><li>About Us</li><li>Our Services</li><li>News</li><li>Contact Us</li></ul>
  </div>
  <div class="footer-col abs" style="left:301px;top:995px">
    <h4>Our Services</h4>
    <ul><li>Suspendisse</li><li>Nullam fermentum</li><li>Integer ornare</li><li>Proin iaculis</li><li>Praesent ac</li></ul>
  </div>
  <div class="footer-col abs" style="left:496px;top:995px">
    <h4>Contact us</h4>
  </div>
  <div class="contact-line abs" style="left:496px;top:1025px"><svg width="9" height="12" viewBox="0 0 10 14"><path d="M5 0a5 5 0 0 1 5 5c0 4-5 9-5 9S0 9 0 5a5 5 0 0 1 5-5z" fill="#8c8c8c"/><circle cx="5" cy="5" r="2" fill="#262626"/></svg><span>48 Harbour Lane Concourse<br>Level Ashford, On K0L 2B4</span></div>
  <div class="contact-line abs" style="left:496px;top:1066px"><svg width="10" height="10" viewBox="0 0 24 24"><path fill="#8c8c8c" d="M6.6 10.8a15 15 0 0 0 6.6 6.6l2.2-2.2a1 1 0 0 1 1-.25 11 11 0 0 0 3.6.6 1 1 0 0 1 1 1V20a1 1 0 0 1-1 1A17 17 0 0 1 3 4a1 1 0 0 1 1-1h3.5a1 1 0 0 1 1 1 11 11 0 0 0 .6 3.6 1 1 0 0 1-.25 1z"/></svg><span>555-014-2290</span></div>
  <div class="contact-line abs" style="left:496px;top:1092px;font-size:8px"><svg width="10" height="8" viewBox="0 0 10 8"><rect width="10" height="8" fill="#8c8c8c"/><path d="M0 0l5 4 5-4" stroke="#262626" fill="none"/></svg><span>info@maplewickhaven.com</span></div>
  <div class="footer-col abs" style="left:742px;top:995px">
    <h4>Newsletter</h4>
  </div>
  <p class="newsletter-text abs" style="left:742px;top:1024px;width:188px">Lorem ipsum dolor sit amet, consectetur adipiscing elit. Nunc eget magna enim.</p>
  <div class="news-input abs">Email Address</div>
  <div class="news-submit abs">Submit</div>

  <div class="bottom-bar abs">
    <span class="copyright abs">All Right Reserved 2015. Maplewick Haven Supply.</span>
    <span class="social abs" style="left:844px"></span>
    <span class="social abs" style="left:878px"></span>
    <span class="social abs" style="left:910px"></span>
  </div>

</div>
</body>
</html>
```